Whitcombe Business Card Design

The name of the business is Dario Whitcombe, CPA LLC
The service that we offer is Accounting, Tax & Consulting Services. I need it to have the following items:
Dario Whitcombe, Principal
Phone Number
Email Address
Physical Address

I have attached the company logo, one in black and one in white. Please provide a design in black background and the other in white background. Please include "Accounting, Tax & Consulting Services". I want the business card to be clean and very professional.

```html
<!DOCTYPE html>
<html lang="en">
<head>
<meta charset="utf-8">
<title>Dario Whitcombe, CPA LLC – Business Cards</title>
<link rel="stylesheet" href="https://fonts.googleapis.com/css2?family=Montserrat:wght@600&family=Arimo:wght@400&display=swap">
<style>
  :root {
    --backdrop: #d9d8d6;
    --card: #ffffff;
    --brand-red: #a3161c;
    --ink: #2f2f31;
    --rule: #8a8a8a;
    --muted: #555555;
  }
  html, body {
    margin: 0;
    width: 1200px;
    height: 801px;
    overflow: hidden;
    background: var(--backdrop);
  }
  .sheet {
    position: relative;
    width: 1200px;
    height: 801px;
    display: flex;
    align-items: center;
    justify-content: center;
    gap: 48px;
  }
  .card {
    position: relative;
    width: 540px;
    height: 309px;
    background: var(--card);
    border-bottom: 5px solid var(--brand-red);
    box-shadow: 0 10px 24px rgba(0,0,0,0.18);
    box-sizing: border-box;
    font-family: "Arimo", Arial, sans-serif;
    color: var(--ink);
  }
  .company-name {
    font-family: "Montserrat", Arial, sans-serif;
    font-weight: 600;
    color: var(--ink);
    margin: 0;
    letter-spacing: 0.2px;
    white-space: nowrap;
  }
  .square-mark {
    display: inline-block;
    width: 12px;
    height: 12px;
    background: var(--brand-red);
    margin-right: 10px;
    vertical-align: middle;
  }

  /* Front */
  .card-front .company-lockup {
    position: absolute;
    right: 36px;
    top: 58px;
    display: flex;
    align-items: center;
  }
  .card-front .company-name { font-size: 17px; }
  .card-front .divider {
    position: absolute;
    left: 36px;
    right: 36px;
    top: 162px;
    height: 1px;
    background: var(--rule);
  }
  .person {
    position: absolute;
    left: 36px;
    top: 104px;
  }
  .person-name {
    font-family: "Montserrat", Arial, sans-serif;
    font-weight: 600;
    font-size: 22px;
    color: var(--brand-red);
    margin: 0;
    text-transform: uppercase;
  }
  .person-title {
    font-size: 14px;
    margin: 4px 0 0;
    color: var(--ink);
  }
  .contact-list {
    position: absolute;
    left: 36px;
    top: 182px;
    list-style: none;
    margin: 0;
    padding: 0;
    font-size: 13.5px;
    line-height: 23px;
  }
  .contact-list li { display: flex; align-items: center; gap: 9px; }
  .contact-list svg { width: 11px; height: 11px; fill: var(--brand-red); flex: none; }
  .address {
    position: absolute;
    right: 36px;
    top: 182px;
    margin: 0;
    font-style: normal;
    text-align: right;
    font-size: 14px;
    line-height: 22px;
  }

  /* Back */
  .card-back .company-lockup {
    position: absolute;
    left: 0;
    right: 0;
    top: 118px;
    display: flex;
    justify-content: center;
    align-items: center;
  }
  .card-back .company-name { font-size: 24px; }
  .tagline {
    position: absolute;
    left: 0;
    right: 0;
    top: 196px;
    text-align: center;
    font-size: 15px;
    margin: 0;
    color: var(--ink);
  }
</style>
</head>
<body>
<main class="sheet">

  <section class="card card-front" aria-label="Business card front">
    <div class="company-lockup">
      <span class="square-mark" aria-hidden="true"></span>
      <p class="company-name">Dario Whitcombe, CPA LLC</p>
    </div>

    <div class="person">
      <h1 class="person-name">Dario Whitcombe</h1>
      <p class="person-title">Principal</p>
    </div>

    <div class="divider" aria-hidden="true"></div>

    <ul class="contact-list">
      <li>
        <svg viewBox="0 0 24 24" aria-hidden="true"><path d="M6.6 10.8a15.1 15.1 0 0 0 6.6 6.6l2.2-2.2c.3-.3.7-.4 1-.2 1.1.4 2.3.6 3.6.6.6 0 1 .4 1 1V20c0 .6-.4 1-1 1A17 17 0 0 1 3 4c0-.6.4-1 1-1h3.5c.6 0 1 .4 1 1 0 1.3.2 2.5.6 3.6.1.3 0 .7-.2 1z"/></svg>
        <span>215-390-2648</span>
      </li>
      <li>
        <svg viewBox="0 0 24 24" aria-hidden="true"><path d="M2 5h20v14H2z M2 5l10 8 10-8" /></svg>
        <span>info@dariowhitcombecpa.com</span>
      </li>
      <li>
        <svg viewBox="0 0 24 24" aria-hidden="true"><circle cx="12" cy="12" r="10"/></svg>
        <span>www.dariowhitcombecpa.com</span>
      </li>
    </ul>

    <address class="address">
      1480 N Alder Lane<br>
      Brookvale County 7720
    </address>
  </section>

  <section class="card card-back" aria-label="Business card back">
    <div class="company-lockup">
      <span class="square-mark" aria-hidden="true"></span>
      <p class="company-name">Dario Whitcombe, CPA LLC</p>
    </div>
    <p class="tagline">Accounting, Tax &amp; Consulting Services</p>
  </section>

</main>
</body>
</html>
```